KRWB new business card design

We need a business card design for our established business which is Australia wide however based in Melbourne. We are a young team of Financial Planners who specialize in Insurance and Basic super advice for people like us.

We are people who help our clients get things done in a timely and cost effective manner whilst having a good time and a laugh along the way.

We would like this to have a consistent feel with our new e-brochure which i have attached from a color and font perspective.

Industry/Entity Type

Business

Requirements
Must have
• We do not need specific address details rather just the states we are in:

VIC/NSW/QLD/TAS
Nice to have
• Curved edge to mate the brochure

```html
<!DOCTYPE html>
<html lang="en">
<head>
<meta charset="utf-8">
<title>KRWB business card</title>
<link rel="stylesheet" href="https://fonts.googleapis.com/css2?family=Arimo:ital,wght@0,400;0,700;1,700&family=PT+Sans&display=swap">
<style>
  :root {
    --stage: #e6e1da;
    --label: #1e1e1e;
    --green: #6cc04a;
    --green-deep: #12a150;
    --ink: #3a3a3a;
    --grey: #6b6b6b;
    --white: #ffffff;
    --black: #050505;
    --faint: #eef2ec;
  }
  * { margin: 0; padding: 0; box-sizing: border-box; }
  html, body { width: 1200px; height: 788px; overflow: hidden; }
  body {
    position: relative;
    background: var(--stage);
    font-family: "Arimo", Arial, sans-serif;
  }
  .side-label {
    position: absolute;
    width: 525px;
    text-align: center;
    font-family: "PT Sans", sans-serif;
    font-size: 22px;
    color: var(--label);
  }
  .card {
    position: absolute;
    width: 525px;
    height: 300px;
    border-radius: 20px;
    overflow: hidden;
    box-shadow: 0 4px 10px rgba(0,0,0,0.35);
  }
  .card--front { left: 53px; top: 72px; background: radial-gradient(ellipse at 50% 35%, #2c2c2c 0%, #0d0d0d 55%, var(--black) 100%); color: var(--white); }
  .card--back1 { left: 622px; top: 74px; background: var(--white); }
  .card--back2 { left: 53px; top: 445px; background: var(--white); }
  .card--back3 { left: 622px; top: 445px; background: linear-gradient(135deg, #2a2a2a, #0b0b0b); color: var(--white); }

  .abs { position: absolute; }
  .mark { position: absolute; background: var(--green); }
  .brand-name { position: absolute; font-weight: 700; text-align: center; line-height: 1; }

  /* Front */
  .front__mark { left: 240px; top: 24px; width: 46px; height: 46px; }
  .front__brand { left: 0; width: 525px; top: 132px; font-size: 22px; color: var(--white); }
  .front__name { left: 0; width: 525px; top: 174px; text-align: center; font-size: 18px; font-weight: 700; color: var(--green); }
  .front__title { left: 0; width: 525px; top: 196px; text-align: center; font-size: 13.5px; font-weight: 700; color: var(--green); }
  .front__contact { left: 0; width: 525px; text-align: center; font-size: 13.5px; color: var(--white); }
  .front__contact b { font-style: italic; }
  .front__band { left: 0; top: 268px; width: 525px; height: 32px; }
  .front__band-text { top: 276px; font-size: 12.5px; color: var(--white); }
  .front__band-text b { font-style: italic; }

  /* Lists */
  .spec-heading { font-size: 18px; font-weight: 700; font-style: italic; }
  .spec-list { list-style: none; }
  .spec-list li { font-size: 14px; font-weight: 700; height: 34px; }
  .spec-list li::before { content: "\25AA\00a0"; }

  /* Back 1 */
  .back1__mark { left: 78px; top: 54px; width: 88px; height: 88px; }
  .back1__brand { left: 40px; width: 200px; top: 200px; font-size: 24px; color: var(--black); }
  .back1__divider { left: 260px; top: 20px; width: 2px; height: 240px; background: linear-gradient(to bottom, transparent, #777, transparent); }
  .back1__spec { left: 320px; top: 46px; color: var(--grey); }
  .back1__spec .spec-list { margin-top: 16px; }
  .back1__band { left: 0; top: 261px; width: 525px; height: 39px; background: var(--green); color: var(--white); font-size: 14px; font-weight: 700; text-align: center; line-height: 34px; }

  /* Back 2 */
  .back2__deco { left: 150px; top: 14px; width: 226px; height: 282px; background: var(--faint); border-radius: 12px; }
  .back2__spec { left: 0; width: 525px; top: 46px; text-align: center; color: var(--ink); }
  .back2__spec .spec-list { margin-top: 16px; }
  .back2__tag { left: 0; width: 525px; top: 268px; text-align: center; font-size: 14px; font-weight: 700; color: var(--ink); }

  /* Back 3 */
  .back3__mark { left: 88px; top: 22px; width: 150px; height: 150px; }
  .back3__brand { left: 40px; width: 250px; top: 216px; font-size: 34px; color: var(--white); }
  .back3__spec { left: 312px; top: 24px; }
  .back3__spec .spec-list { margin-top: 16px; }
  .back3__tag { left: 313px; top: 254px; font-size: 14px; font-weight: 700; color: var(--green); line-height: 18px; }
</style>
</head>
<body>
  <div class="side-label" style="left:53px; top:34px;">Front</div>
  <div class="side-label" style="left:622px; top:34px;">Back - 1</div>
  <div class="side-label" style="left:53px; top:404px;">Back - 2</div>
  <div class="side-label" style="left:622px; top:404px;">Back - 3</div>

  <section class="card card--front">
    <div class="mark front__mark"></div>
    <div class="brand-name front__brand">Kestrel Ridge</div>
    <div class="abs front__name">Daniel Morrow</div>
    <div class="abs front__title">ADFS, BBus, LRS© - Financial Adviser</div>
    <div class="abs front__contact" style="top:221px;"><b>cell</b> 0412 555 018 &nbsp;| &nbsp;<b>phone</b> 1300 555 274</div>
    <div class="abs front__contact" style="top:243px;"><b>fax</b> 03 9555 0142 &nbsp;| &nbsp;VIC/NSW/QLD/TAS</div>
    <svg class="abs front__band" viewBox="0 0 525 32" aria-hidden="true">
      <polygon points="0,0 232,0 262,32 0,32" fill="var(--green)"/>
      <polygon points="232,0 244,0 274,32 262,32" fill="#0c0c0c"/>
      <polygon points="244,0 525,0 525,32 274,32" fill="var(--green-deep)"/>
    </svg>
    <div class="abs front__band-text" style="left:62px;"><b>e</b> daniel@krwb.com.au</div>
    <div class="abs front__band-text" style="left:333px;"><b>w</b> www.krwb.com.au</div>
  </section>

  <section class="card card--back1">
    <div class="mark back1__mark"></div>
    <div class="brand-name back1__brand">Kestrel Ridge</div>
    <div class="abs back1__divider"></div>
    <div class="abs back1__spec">
      <div class="spec-heading">Specialising in</div>
      <ul class="spec-list">
        <li>Risk Insurance</li>
        <li>Debt Management</li>
        <li>Superannuation</li>
        <li>Wealth Creation</li>
        <li>Retirement Planning</li>
      </ul>
    </div>
    <div class="abs back1__band">SECURE FUTURE, ENHANCED LIFESTYLE</div>
  </section>

  <section class="card card--back2">
    <div class="abs back2__deco"></div>
    <div class="abs back2__spec">
      <div class="spec-heading">Specialising in</div>
      <ul class="spec-list">
        <li>Risk Insurance</li>
        <li>Debt Management</li>
        <li>Superannuation</li>
        <li>Wealth Creation</li>
        <li>Retirement Planning</li>
      </ul>
    </div>
    <div class="abs back2__tag">SECURE FUTURE, ENHANCED LIFESTYLE</div>
  </section>

  <section class="card card--back3">
    <div class="mark back3__mark"></div>
    <div class="brand-name back3__brand">Kestrel Ridge</div>
    <div class="abs back3__spec">
      <div class="spec-heading">Specialising in</div>
      <ul class="spec-list">
        <li>Risk Insurance</li>
        <li>Debt Management</li>
        <li>Superannuation</li>
        <li>Wealth Creation</li>
        <li>Retirement Planning</li>
      </ul>
    </div>
    <div class="abs back3__tag">SECURE FUTURE<br>ENHANCED LIFESTYLE</div>
  </section>
</body>
</html>
```